The Orchard of Renewal Book Cover Contest

Book Cover Design (front, spine, and back) 6" x 9" (152.4 x 228.6 mm) book use the attached images(_4ec9c7... or Background image) on cover, or just as inspiration, or not at all.
Genre: Non-Fiction, Christian, Health, Self-Help
Book Title: The Orchard of Renewal
Sub text: with Annotated Original Page Numbers, Index, and Appendix of Supporting Scientific Research.
Author: Marta J. Crandall
Summary on back of book:
The Orchard of Renewal is a timeless classic that was written over a century ago, containing life-changing principles for health and healing that continue to impact and save lives today. This book examines the life and teachings of the Master Physician (Jesus Christ) and provides practical advice.
Recent scientific advancements in the last 30 years have started to uncover some of the reasons behind why these healthful principles work. Many physicians and doctors have studied and continue to share this book, including notable names like Dorris Pemberton. It is our honor to offer the "Orchard of Renewal" with annotated original page numbers, index, and an appendix of supporting scientific research and additional supporting resources to help readers fully understand and apply this valuable content in their health journey and sharing with others.
I like text layered in with images (example1&2). Examples attached but use your own creativity.
Thank you for your help!
Target Market(s)
Stressed, sick, and tired women and men
Industry/Entity Type
Non-Fiction, Christian, Health, Self-Help
Colors
Designer to choose colors to be used in the design.
Look and feel
Each slider illustrates characteristics of the customer's brand and the style your logo design should communicate.

```html
<!DOCTYPE html>
<html lang="en">
<head>
<meta charset="utf-8">
<title>The Orchard of Renewal – Cover Wrap</title>
<link href="https://fonts.googleapis.com/css2?family=Bebas+Neue&family=Rubik:wght@600&family=Roboto:wght@400&display=swap" rel="stylesheet">
<style>
  :root{
    --page-bg:#e9ebe1;
    --sky-top:#0f3553;
    --sky-upper:#1d5a84;
    --sky-mid:#3b86b3;
    --sky-low:#94b6c6;
    --glow:#ef8a6c;
    --glow-soft:#f3b08e;
    --hill:#232a35;
    --hill-deep:#151a22;
    --gold:#ecd23f;
    --white:#ffffff;
    --spine-shade:rgba(0,0,0,.18);
  }
  *{margin:0;padding:0;box-sizing:border-box}
  html,body{width:1200px;height:1200px;overflow:hidden;background:var(--page-bg)}
  .wrap{
    position:absolute;left:28px;top:204px;width:1144px;height:792px;
    display:flex;
    box-shadow:0 14px 40px rgba(0,0,0,.18);
  }
  .sky{
    position:absolute;inset:0;
    background:linear-gradient(180deg,var(--sky-top) 0%,var(--sky-upper) 22%,var(--sky-mid) 48%,var(--sky-low) 64%,var(--glow-soft) 72%,var(--glow) 78%,var(--hill) 84%,var(--hill-deep) 100%);
  }
  .panel{position:relative;height:100%}
  .back{width:528px}
  .spine{width:88px;background:var(--spine-shade)}
  .front{width:528px}

  /* back */
  .back-title{
    position:absolute;top:86px;left:0;width:100%;text-align:center;
    font-family:'Bebas Neue',sans-serif;font-size:58px;line-height:1;color:var(--white);
  }
  .accent{color:var(--gold)}
  .back-subtitle{
    position:absolute;top:156px;left:0;width:100%;text-align:center;
    font-family:'Rubik',sans-serif;font-weight:600;font-size:12.5px;line-height:1.35;color:var(--gold);
  }
  .back-copy{
    position:absolute;top:212px;left:44px;width:440px;
    font-family:'Roboto',sans-serif;font-size:12.2px;line-height:1.52;color:var(--white);
    text-align:justify;text-align-last:center;
  }
  .back-copy p+p{margin-top:18px}

  /* spine */
  .spine-text{
    position:absolute;left:0;top:34px;width:100%;height:724px;
    writing-mode:vertical-rl;display:flex;align-items:center;
  }
  .spine-title{font-family:'Bebas Neue',sans-serif;font-size:34px;color:var(--white);line-height:1}
  .spine-subtitle{
    margin-top:34px;font-family:'Rubik',sans-serif;font-weight:600;font-size:9px;line-height:1.25;
    color:var(--gold);text-align:center;
  }
  .spine-author{
    margin-top:auto;font-family:'Bebas Neue',sans-serif;font-size:24px;letter-spacing:3px;color:var(--white);
  }

  /* front */
  .front-figure{
    position:absolute;left:70px;right:0;top:300px;bottom:0;
    background:radial-gradient(ellipse at 60% 55%,rgba(90,70,60,.55) 0%,rgba(60,60,70,.35) 40%,rgba(0,0,0,0) 70%);
  }
  .front-subtitle{
    position:absolute;top:36px;left:0;width:100%;text-align:center;
    font-family:'Rubik',sans-serif;font-weight:600;font-size:14.5px;line-height:1.35;color:var(--gold);
  }
  .front-title{
    position:absolute;top:88px;left:36px;width:456px;
    font-family:'Bebas Neue',sans-serif;color:var(--white);text-align:center;line-height:.9;
  }
  .front-title .line-one{display:block;font-size:88px}
  .front-title .line-two{display:block;font-size:158px;color:var(--gold);margin-top:-4px}
  .front-author{
    position:absolute;left:34px;bottom:70px;
    font-family:'Bebas Neue',sans-serif;font-size:52px;letter-spacing:2px;color:var(--white);
  }
</style>
</head>
<body>
  <div class="wrap">
    <div class="sky" role="img" aria-label="Sunset sky fading from deep blue to pink glow over dark hills"></div>

    <section class="panel back">
      <h2 class="back-title">The Orchard of <span class="accent">Renewal</span></h2>
      <p class="back-subtitle">WITH ANNOTATED ORIGINAL PAGE NUMBERS, INDEX, AND<br>APPENDIX OF SUPPORTING SCIENTIFIC RESEARCH</p>
      <div class="back-copy">
        <p>Lorem ipsum dolor sit amet, consectetur adipiscing elit, sed do eiusmod tempor incididunt ut labore et dolore magna aliqua. Quis ipsum suspendisse ultrices gravida. Risus commodo viverra maecenas accumsan lacus vel facilisis. Lorem ipsum dolor sit amet, consectetur adipiscing elit, sed do eiusmod tempor incididunt ut labore et dolore magna aliqua. Quis ipsum suspendisse ultrices gravida. Risus commodo viverra maecenas accumsan lacus vel facilisis. Lorem ipsum dolor sit amet, consectetur adipiscing elit, sed do eiusmod tempor incididunt ut labore et dolore magna aliqua. Quis ipsum suspendisse ultrices gravida. Risus commodo viverra maecenas accumsan lacus vel facilisis.</p>
        <p>Lorem ipsum dolor sit amet, consectetur adipiscing elit, sed do eiusmod tempor incididunt ut labore et dolore magna aliqua. Quis ipsum suspendisse ultrices gravida. Risus commodo viverra maecenas accumsan lacus vel facilisis. Lorem ipsum dolor sit amet, consectetur adipiscing elit, sed do eiusmod tempor incididunt ut labore et dolore magna aliqua. Quis ipsum suspendisse ultrices gravida. Risus commodo viverra maecenas accumsan lacus vel facilisis. Lorem ipsum dolor sit amet, consectetur adipiscing elit, sed do eiusmod tempor incididunt ut labore et dolore magna aliqua. Quis ipsum suspendisse ultrices gravida. Risus commodo viverra maecenas accumsan lacus vel facilisis.</p>
      </div>
    </section>

    <section class="panel spine">
      <div class="spine-text">
        <span class="spine-title">THE ORCHARD OF <span class="accent">RENEWAL</span></span>
        <span class="spine-subtitle">WITH ANNOTATED ORIGINAL PAGE NUMBERS, INDEX, AND<br>APPENDIX OF SUPPORTING SCIENTIFIC RESEARCH</span>
        <span class="spine-author">MARTA J. CRANDALL</span>
      </div>
    </section>

    <section class="panel front">
      <div class="front-figure" role="img" aria-label="Bearded man in a wet white shirt raising one hand toward the sky in praise, a cross on a distant hill at sunrise"></div>
      <p class="front-subtitle">WITH ANNOTATED ORIGINAL PAGE NUMBERS, INDEX, AND<br>APPENDIX OF SUPPORTING SCIENTIFIC RESEARCH</p>
      <h1 class="front-title">
        <span class="line-one">THE ORCHARD OF</span>
        <span class="line-two">RENEWAL</span>
      </h1>
      <p class="front-author">MARTA J. CRANDALL</p>
    </section>
  </div>
</body>
</html>
```